Brochure for a new technology in mineral processing industry

We require a rush design for a brochure for an upcoming conference on 8th December. It needs to comply with our logo colours and web site (www.krelvantech.com.au). The attached is a mockup (not very creative) that should be used as a guide only. A word version is available upon request. The design should be aligned with a science and engineering based organisation and not be too busy in its design. Looking for classic but simple lines. Photos loaded up should be used at the designers discretion to enhance look.

Target Market(s)

Brochure to be used to market to mining industry.

Industry/Entity Type

Mining

Requirements
Must have
• The brochure must have simple lines - not to be busy. Colours to match logo and corporate colours and website branding.
Nice to have
• Themes that we feel would be nice to bring through:
• 1. Step Change/modern/innovation
• 2. Clever science being commercialised
• 3. Mining Industry
Should not have
• Not too busy. Arty perspectives.

```html
<!DOCTYPE html>
<html lang="en">
<head>
<meta charset="utf-8">
<title>Technology – Azurel Technology Services</title>
<link href="https://fonts.googleapis.com/css2?family=Montserrat:wght@400;700&display=swap" rel="stylesheet">
<style>
  :root {
    --page: #ffffff;
    --green: #8cc63f;
    --ink: #2f3341;
    --rock-a: #c8622a;
    --rock-b: #8e4a2a;
    --flask-a: #3d7bd8;
    --flask-b: #9aa3ad;
    --lab-a: #2a2a2c;
    --lab-b: #d9d6cf;
  }
  * { box-sizing: border-box; margin: 0; padding: 0; }
  html, body { width: 848px; height: 1200px; overflow: hidden; background: var(--page); }
  .page {
    position: relative; width: 848px; height: 1200px; overflow: hidden;
    background: var(--page);
    font-family: "Montserrat", Arial, sans-serif; color: var(--ink);
  }
  .content { position: relative; padding: 58px 70px 0 70px; font-size: 16.5px; line-height: 20.5px; }
  .page-title { color: var(--green); font-weight: 400; font-size: 22.5px; line-height: 28px; margin-bottom: 25px; }
  .intro { margin-bottom: 20px; }
  .section-title { font-weight: 700; font-size: 16.5px; margin-top: 21.5px; }
  .service-list { list-style: none; }
  .service-list li::before { content: "\2022\00a0"; padding-left: 2px; }
  .gallery { position: absolute; left: 0; top: 825px; width: 848px; height: 375px; display: flex; }
  .photo { height: 100%; }
  .photo--ore { width: 266px; background: linear-gradient(160deg, var(--rock-a), var(--rock-b) 60%, #e9ecef 85%); }
  .photo--flasks { width: 294px; background: linear-gradient(200deg, #e8e8e6, var(--flask-b) 40%, var(--flask-a) 80%); }
  .photo--reactor { width: 288px; background: linear-gradient(180deg, #f2f2f0, var(--lab-b) 35%, var(--lab-a) 75%); }
</style>
</head>
<body>
<div class="page">
  <main class="content">
    <h1 class="page-title">Technology</h1>
    <p class="intro">Azurel Technology Services focus on developing robust, safe and innovative processing solutions for your mine site.&nbsp; Our services include:</p>
    <ul class="service-list">
      <li>Mineral Processing, Design &amp; Development</li>
      <li>Commercial Scale Pilot Plant (CSPP) Integration</li>
      <li>Flowsheet modernization</li>
      <li>Metallurgical data management</li>
      <li>Reagent Design, Development, &amp; Maintenance</li>
      <li>Process Plant Solutions</li>
      <li>Verification &amp; Validation Service</li>
    </ul>

    <h2 class="section-title">Processing Technology Services:</h2>
    <ul class="service-list">
      <li>Ore leaching trials, process modernization and conversion</li>
      <li>Hydrometallurgy, flotation, filtration, calcination and other engineered system implementation</li>
      <li>Pilot Plant Operations (PPO) Upgrade and Management</li>
      <li>Reactor control system implementation and administration</li>
      <li>Process High Availability (HA) implementation with continuous sampling and onsite QA</li>
      <li>Jacketed reactor 12L upgrade and migration</li>
      <li>Laboratory Analysis Manager implementation and sample upgrade</li>
      <li>Site Safety and Access Management implementation</li>
      <li>Bench Scale Appliance (BSA) implementation</li>
    </ul>

    <h2 class="section-title">Laboratory Technology Services:</h2>
    <ul class="service-list">
      <li>Assay laboratory implementation and training</li>
      <li>Sample migration from field sites and others to laboratory platform</li>
      <li>Assay method upgrade and migration</li>
      <li>Reagent handling implementation and training</li>
    </ul>

    <h2 class="section-title">Commercialisation Technology Services:</h2>
    <ul class="service-list">
      <li>Clever science implementation at mine sites</li>
      <li>Technology scale-up from laboratory to full plant</li>
    </ul>
  </main>

  <div class="gallery">
    <div class="photo photo--ore" role="img" aria-label="Close-up of orange mineral ore pieces beside white crystals"></div>
    <div class="photo photo--flasks" role="img" aria-label="Laboratory round-bottom flasks filled with blue liquid"></div>
    <div class="photo photo--reactor" role="img" aria-label="Jacketed glass reactor with control units in a laboratory"></div>
  </div>
</div>
</body>
</html>
```